MintVela business cards

We want to create two sets of cards. One general card for mintvela [staff] and one card for the founder of the company. Below is the general/basic information for you to format/display on side of the cards:
--Company address: 418 Larkmoor Street, New York, NY 10087
--Main phone: 212-736-5182
Will also provide you with secondary 1-800-736-5190
--company website: www.mintvela.example
--email address for general card: frontdesk@mintvela.example
--email address (for dr hollings's card: md@mintvela.example
--titles for dr hollings's card: Founder, Medical Director
--Dr. Hollings's name on the card should read: Gregor T. Hollings, MD
You can also play around with mintvela's tag line: Quiet Glow Keeps Its Promise (TM or R should be attached as a trademark has been filed)
Reason: More time to design something awesome. This company is an aesthetic medical company that offers cool and safe cosmetic treatments
For the business card design for the doctor, please change the doctor's name to look like this above his title: Gregor T. Hollings, MD instead of using Dr. Gregor....etc
Reason: WILL NOT BE ABLE TO VIEW AND FINALIZE DESIGNS UNTIL I RETURN FROM MEDICAL CONFERENCE, WHICH WILL BE ON SUNDAY/MONDAY. MY APOLOGIES
can everyone try making it very minimalistic
A Bit of a change...
Can everyone take a stab at using a grey "raw" or eco friendly stock paper. We are interested to see the designs you come up with.
Business

```html
<!DOCTYPE html>
<html lang="en">
<head>
<meta charset="utf-8">
<title>MintVela business cards</title>
<link href="https://fonts.googleapis.com/css2?family=Open+Sans:wght@300;400;600;700&display=swap" rel="stylesheet">
<style>
  :root {
    --page-bg: #2b2d30;
    --stock-light: #eceae6;
    --stock-shade: #dedcd7;
    --brand-blue: #3f8fd2;
    --brand-blue-light: #6fb3e2;
    --ink-dark: #34373c;
    --ink-soft: #5f646c;
    --band-grey: #9fa2a6;
    --band-text: #ffffff;
  }
  * { margin: 0; padding: 0; box-sizing: border-box; }
  html, body { width: 1200px; height: 862px; overflow: hidden; }
  body {
    background: var(--page-bg);
    font-family: "Open Sans", Arial, sans-serif;
    position: relative;
  }
  .card {
    position: absolute;
    width: 660px;
    height: 377px;
    left: 270px;
    background: linear-gradient(160deg, var(--stock-light) 0%, var(--stock-shade) 100%);
    border-radius: 3px;
    box-shadow: 0 14px 30px rgba(0,0,0,0.45);
    overflow: hidden;
  }
  .card--front { top: 36px; }
  .card--back { top: 449px; }

  .brand {
    display: flex;
    align-items: flex-start;
    gap: 4px;
  }
  .brand__name {
    font-weight: 400;
    color: var(--brand-blue);
    letter-spacing: -1px;
    line-height: 1;
  }
  .brand__dot {
    width: 9px; height: 9px;
    border-radius: 50%;
    background: var(--brand-blue);
    margin-top: 8px;
  }
  .tagline {
    font-size: 10px;
    letter-spacing: 2.4px;
    text-transform: uppercase;
    color: var(--brand-blue-light);
    margin-top: 6px;
  }
  .tagline sup { font-size: 7px; letter-spacing: 0; }

  .card--front .lockup {
    position: absolute;
    left: 50%; top: 50%;
    transform: translate(-50%, -50%);
    text-align: center;
  }
  .card--front .brand { justify-content: center; }
  .card--front .brand__name { font-size: 76px; }

  .card--back .lockup {
    position: absolute;
    right: 52px; top: 88px;
    text-align: center;
  }
  .card--back .brand__name { font-size: 62px; }

  .person {
    position: absolute;
    left: 40px; top: 124px;
  }
  .person__name {
    font-size: 19px;
    font-weight: 700;
    letter-spacing: 0.6px;
    text-transform: uppercase;
    color: var(--ink-dark);
  }
  .person__first { color: var(--brand-blue); }
  .person__title {
    font-size: 10.5px;
    font-weight: 600;
    letter-spacing: 1.4px;
    text-transform: uppercase;
    color: var(--ink-soft);
    margin-top: 2px;
  }
  .contacts {
    list-style: none;
    margin-top: 16px;
  }
  .contacts li {
    display: flex;
    align-items: center;
    gap: 8px;
    font-size: 10.5px;
    color: var(--ink-soft);
    line-height: 19px;
  }
  .contacts svg { width: 11px; height: 11px; flex: none; }

  .card-band {
    position: absolute;
    left: 0; bottom: 0;
    width: 660px; height: 120px;
  }
  .address {
    position: absolute;
    right: 34px; bottom: 34px;
    font-size: 12.5px;
    color: var(--band-text);
    letter-spacing: 0.3px;
  }
</style>
</head>
<body>

  <section class="card card--front">
    <div class="lockup">
      <div class="brand">
        <span class="brand__name">mintvela</span>
        <span class="brand__dot"></span>
      </div>
      <p class="tagline">Quiet Glow Keeps Its Promise<sup>™</sup></p>
    </div>
  </section>

  <section class="card card--back">
    <svg class="card-band" viewBox="0 0 660 120" preserveAspectRatio="none" aria-hidden="true">
      <path d="M290 120 L290 92 C300 62 312 50 340 50 L660 50 L660 120 Z" fill="var(--band-grey)"/>
      <path d="M0 92 L268 92 C286 92 292 82 300 68 C308 54 318 44 342 44 L660 44"
            fill="none" stroke="var(--brand-blue)" stroke-width="5"/>
    </svg>

    <div class="person">
      <h1 class="person__name"><span class="person__first">Gregor T.</span> Hollings, MD</h1>
      <p class="person__title">Founder, Medical Director</p>
      <ul class="contacts">
        <li>
          <svg viewBox="0 0 12 12"><path d="M2.5 1 L4.5 1 L5.3 3.5 L4 4.5 C4.6 6 6 7.4 7.5 8 L8.5 6.7 L11 7.5 L11 9.5 C11 10.3 10.3 11 9.5 11 C5 11 1 7 1 2.5 C1 1.7 1.7 1 2.5 1 Z" fill="var(--brand-blue)"/></svg>
          212-736-5182
        </li>
        <li>
          <svg viewBox="0 0 12 12"><path d="M2.5 1 L4.5 1 L5.3 3.5 L4 4.5 C4.6 6 6 7.4 7.5 8 L8.5 6.7 L11 7.5 L11 9.5 C11 10.3 10.3 11 9.5 11 C5 11 1 7 1 2.5 C1 1.7 1.7 1 2.5 1 Z" fill="var(--brand-blue)"/></svg>
          1-800-736-5190
        </li>
        <li>
          <svg viewBox="0 0 12 12"><rect x="0.5" y="2" width="11" height="8" fill="var(--brand-blue)"/><path d="M0.5 2 L6 6.5 L11.5 2" fill="none" stroke="#fff" stroke-width="1"/></svg>
          md@mintvela.example
        </li>
        <li>
          <svg viewBox="0 0 12 12"><circle cx="6" cy="6" r="5.2" fill="none" stroke="var(--brand-blue)" stroke-width="1.3"/><path d="M1 6 H11 M6 1 C3.5 3.5 3.5 8.5 6 11 M6 1 C8.5 3.5 8.5 8.5 6 11" fill="none" stroke="var(--brand-blue)" stroke-width="1"/></svg>
          www.mintvela.example
        </li>
      </ul>
    </div>

    <div class="lockup">
      <div class="brand">
        <span class="brand__name">mintvela</span>
        <span class="brand__dot"></span>
      </div>
      <p class="tagline">Quiet Glow Keeps Its Promise<sup>™</sup></p>
    </div>

    <p class="address">418 Larkmoor Street, New York, NY 10087</p>
  </section>

</body>
</html>
```